Need Business Card ASAP

We need a business card design for a meeting coming up in a few days. The company name is Harlow Ridge Building and Construction and the logo is attached. Something clean, cool, and contemporary that we can get to a printer right away. Attached is the business card for Volmar Energy, an affiliated company, which we like. Instead of the hawk on the back, you could use the attached "D". We'll also be needing matching letterhead in the near future, so ideas for that are welcome.

```html
<!DOCTYPE html>
<html lang="en">
<head>
<meta charset="utf-8">
<title>Harlow Ridge Building &amp; Construction — Business Card</title>
<link rel="stylesheet" href="https://fonts.googleapis.com/css2?family=Source+Sans+3:wght@400;600;700&display=swap">
<style>
  :root {
    --backdrop: #e9e6dc;
    --paper: #ffffff;
    --olive-deep: #bcb888;
    --olive-light: #dedbc6;
    --ink: #1f1f1f;
    --ink-soft: #555450;
    --white: #ffffff;
  }
  * { margin: 0; padding: 0; box-sizing: border-box; }
  html, body {
    width: 1034px; height: 1200px; overflow: hidden;
    background: var(--backdrop);
    font-family: "Source Sans 3", "Myriad Pro", Arial, sans-serif;
    color: var(--ink);
  }
  .canvas { position: relative; width: 1034px; height: 1200px; }

  .card {
    position: absolute;
    box-shadow: 0 4px 14px rgba(0,0,0,.25);
    overflow: hidden;
  }

  /* Front */
  .card--front { left: 68px; top: 64px; width: 888px; height: 506px; display: flex; }
  .front-brand {
    position: relative; width: 428px; height: 100%;
    background: var(--paper);
    border-right: 3px solid var(--ink);
  }
  .front-brand__edge {
    position: absolute; left: 0; top: 0; width: 11px; height: 100%;
    background: var(--ink);
  }
  .brand-block {
    position: absolute; left: 91px; top: 85px; width: 269px; height: 341px;
    background: linear-gradient(135deg, var(--olive-deep), var(--olive-light));
    display: flex; align-items: center; justify-content: center;
    text-align: center;
  }
  .brand-block__name {
    font-weight: 600; font-size: 38px; line-height: 1.15;
    color: var(--ink); padding: 0 22px;
  }

  .front-details {
    flex: 1;
    background: linear-gradient(180deg, var(--olive-deep), var(--olive-light));
    padding: 50px 0 0 64px;
  }
  .person__name { font-weight: 700; font-size: 34px; line-height: 1.1; }
  .person__title { font-weight: 700; font-size: 22px; margin-top: 4px; }

  .contact-list { list-style: none; margin-top: 16px; }
  .contact-list__item {
    display: flex; align-items: center; gap: 10px;
    font-size: 25px; line-height: 41px;
  }
  .contact-list__icon { width: 18px; height: 18px; flex: none; fill: var(--ink); }

  .company { margin-top: 18px; }
  .company__name { font-weight: 600; font-size: 29px; line-height: 1.2; }
  .company__address { font-size: 23px; line-height: 1.3; color: var(--ink-soft); margin-top: 8px; }

  /* Back */
  .card--back {
    left: 73px; top: 608px; width: 886px; height: 504px;
    background: linear-gradient(180deg, var(--olive-deep), var(--olive-light));
    display: flex; align-items: center; justify-content: center;
  }
  .back-name {
    font-weight: 600; font-size: 64px; line-height: 1.1;
    color: var(--white); text-align: center;
  }
</style>
</head>
<body>
<main class="canvas">

  <section class="card card--front" aria-label="Business card front">
    <div class="front-brand">
      <div class="front-brand__edge"></div>
      <div class="brand-block">
        <p class="brand-block__name">Harlow Ridge Building &amp; Construction</p>
      </div>
    </div>

    <div class="front-details">
      <h1 class="person__name">Your Name</h1>
      <p class="person__title">Title</p>

      <ul class="contact-list">
        <li class="contact-list__item">
          <svg class="contact-list__icon" viewBox="0 0 20 20" aria-hidden="true"><circle cx="10" cy="10" r="9" fill="none" stroke="#1f1f1f" stroke-width="1.6"/><path d="M6.5 5.5l2 2-1 1.3c.7 1.5 1.8 2.6 3.3 3.3l1.3-1 2 2-1.4 1.6C9.5 14.5 5.5 10.5 5 7z"/></svg>
          (123) 456-7890
        </li>
        <li class="contact-list__item">
          <svg class="contact-list__icon" viewBox="0 0 20 20" aria-hidden="true"><rect x="5" y="1" width="10" height="18" rx="2"/><rect x="7" y="4" width="6" height="8" fill="#d4d0b0"/></svg>
          (123) 456-7890
        </li>
        <li class="contact-list__item">
          <svg class="contact-list__icon" viewBox="0 0 20 20" aria-hidden="true"><path d="M1 8l9-6 9 6v10H1z"/><path d="M2 8l8 5 8-5" fill="none" stroke="#d4d0b0" stroke-width="1.4"/></svg>
          yourname@harlowridge.com
        </li>
        <li class="contact-list__item">
          <svg class="contact-list__icon" viewBox="0 0 20 20" aria-hidden="true"><circle cx="10" cy="10" r="9"/><path d="M1 10h18M10 1c-4 4-4 14 0 18M10 1c4 4 4 14 0 18" fill="none" stroke="#d4d0b0" stroke-width="1.2"/></svg>
          www.harlowridge.com
        </li>
      </ul>

      <div class="company">
        <h2 class="company__name">Harlow Ridge Building<br>&amp; Construction</h2>
        <p class="company__address">00, Complex Name, Street<br>City 00000</p>
      </div>
    </div>
  </section>

  <section class="card card--back" aria-label="Business card back">
    <p class="back-name">Harlow Ridge</p>
  </section>

</main>
</body>
</html>
```